Salon Signage

We need a new company sign designed for the exterior of our salon. I have attached our current logos for an idea. I have also attached a photo of what salon looks like currently.

```html
<!DOCTYPE html>
<html lang="en">
<head>
<meta charset="utf-8">
<title>Glosswave Beauty Salon – Exterior Sign</title>
<link rel="stylesheet" href="https://fonts.googleapis.com/css2?family=Archivo:wght@900&family=Montserrat:wght@700&family=Sacramento&display=swap">
<style>
  :root {
    --bg-light: #f8e6e1;
    --bg-warm: #f4ddd7;
    --ink: #1c1b19;
    --plum: #a2268a;
    --magenta: #d61b78;
    --white: #ffffff;
    --emblem-outer: #ead0c9;
    --emblem-inner: #8a5a4a;
  }
  html, body {
    margin: 0;
    padding: 0;
    width: 1200px;
    height: 301px;
    overflow: hidden;
    background: var(--bg-light);
  }
  .sign {
    display: block;
    width: 1200px;
    height: 301px;
  }
  .brand-name {
    font-family: "Archivo", "Arial Black", sans-serif;
    font-weight: 900;
    font-size: 158px;
    fill: var(--ink);
  }
  .brand-tagline {
    font-family: "Sacramento", cursive;
    font-size: 98px;
    fill: var(--ink);
  }
  .phone-number {
    font-family: "Montserrat", Arial, sans-serif;
    font-weight: 700;
    font-size: 56px;
    fill: var(--white);
  }
</style>
</head>
<body>
<svg class="sign" viewBox="0 0 1200 301" xmlns="http://www.w3.org/2000/svg">
  <defs>
    <linearGradient id="sign-bg" x1="0" y1="0" x2="1" y2="0">
      <stop offset="0" stop-color="var(--bg-light)"/>
      <stop offset="1" stop-color="var(--bg-warm)"/>
    </linearGradient>
    <linearGradient id="phone-band" x1="0" y1="0" x2="1" y2="0">
      <stop offset="0" stop-color="var(--plum)"/>
      <stop offset="1" stop-color="var(--magenta)"/>
    </linearGradient>
    <radialGradient id="emblem-fill" cx="0.5" cy="0.5" r="0.5">
      <stop offset="0" stop-color="var(--emblem-inner)"/>
      <stop offset="0.55" stop-color="#c79a8c"/>
      <stop offset="1" stop-color="var(--emblem-outer)"/>
    </radialGradient>
  </defs>

  <rect class="background" width="1200" height="301" fill="url(#sign-bg)"/>

  <circle class="emblem" cx="191" cy="151" r="135" fill="url(#emblem-fill)"
          role="img" aria-label="Illustrated stylist holding hair tools: dryer, brush, scissors, colour swatches and straightener"/>

  <text class="brand-name" x="359" y="149" textLength="801" lengthAdjust="spacingAndGlyphs">GLOSSWAVE</text>

  <text class="brand-tagline" x="354" y="228" textLength="390" lengthAdjust="spacingAndGlyphs">Beauty Salon</text>

  <polygon class="phone-band" points="787,241 826,171 1200,171 1200,241" fill="url(#phone-band)"/>
  <text class="phone-number" x="794" y="223" textLength="362" lengthAdjust="spacingAndGlyphs">(03) 9555 0147</text>

  <polygon class="base-stripe" points="0,291 760,291 752,301 0,301" fill="var(--plum)"/>
</svg>
</body>
</html>
```